Redesign current business card for food company

i would like to redesign my business card. our company is food company, our product range from chips, juices, milk and etc (mostly dried food stuff).
I want o keep same logo but , the rest is open to new design.
you can check at our website about our company www.orvelpantry.com

Target Market(s)

most of food company

Industry/Entity Type

Business

Contact Information for Business Card

I want to keep more to blue color...

Colors
3176b5
abd036

Requirements
Must have
• our old logo
Nice to have
• we do not mind to have nice material on bus card in order to accomplish nice design. for example: using spot uv, embossed and etc.

```html
<!DOCTYPE html>
<html lang="en">
<head>
<meta charset="utf-8">
<title>Orvel Enterprises – Business Card</title>
<link href="https://fonts.googleapis.com/css2?family=Questrial&display=swap" rel="stylesheet">
<style>
  :root {
    --page: #e9ebef;
    --paper: #fbfbfb;
    --ink: #1d1f24;
    --brand-blue: #2f4fc4;
    --deep-blue: #2b3aa8;
    --cyan: #19b9d2;
    --white: #ffffff;
  }
  * { margin: 0; padding: 0; box-sizing: border-box; }
  html, body { width: 1200px; height: 780px; overflow: hidden; }
  body {
    background: var(--page);
    font-family: "Questrial", "Helvetica Neue", Arial, sans-serif;
    color: var(--ink);
    display: flex;
    align-items: center;
    justify-content: center;
    gap: 40px;
  }
  .card {
    position: relative;
    width: 560px;
    height: 320px;
    border-radius: 18px;
    overflow: hidden;
    box-shadow: 0 10px 30px rgba(20, 30, 60, 0.18);
  }

  /* Front */
  .card-front { background: var(--paper); }
  .brand-name {
    position: absolute;
    left: 44px;
    top: 92px;
    font-size: 72px;
    line-height: 1;
    color: var(--brand-blue);
  }
  .company-name {
    position: absolute;
    right: 36px;
    top: 34px;
    font-size: 20px;
    letter-spacing: 0.3px;
  }
  .person {
    position: absolute;
    left: 150px;
    width: 280px;
    top: 158px;
    text-align: right;
  }
  .person .name { font-size: 18px; line-height: 22px; }
  .person .rule {
    height: 1.5px;
    background: var(--brand-blue);
    margin-top: 5px;
  }
  .person .title {
    position: absolute;
    left: 286px;
    top: 24px;
    font-size: 14px;
    color: var(--brand-blue);
    white-space: nowrap;
  }
  .contact-list {
    position: absolute;
    left: 150px;
    top: 204px;
    list-style: none;
    font-size: 14px;
    line-height: 20px;
  }
  .contact-list li { display: flex; align-items: center; gap: 8px; }
  .contact-list svg { width: 14px; height: 14px; flex: none; }
  .address {
    position: absolute;
    right: 30px;
    top: 206px;
    text-align: right;
    font-size: 14px;
    line-height: 20px;
  }
  .web-band {
    position: absolute;
    right: 0;
    bottom: 0;
    width: 190px;
    height: 46px;
    background: var(--deep-blue);
    color: var(--white);
    font-size: 14px;
    display: flex;
    align-items: center;
    justify-content: center;
  }

  /* Back */
  .card-back {
    background: radial-gradient(ellipse at 50% 60%, var(--cyan) 0%, #1f7fcf 45%, var(--deep-blue) 100%);
    display: flex;
    align-items: center;
    justify-content: center;
  }
  .card-back .brand-name-large {
    font-size: 120px;
    line-height: 1;
    color: var(--white);
  }
</style>
</head>
<body>
  <section class="card card-front" aria-label="Business card front">
    <p class="brand-name">orvel</p>
    <p class="company-name">Orvel Enterprises Corp.</p>
    <div class="person">
      <p class="name">Daniel Hartono</p>
      <div class="rule"></div>
      <p class="title">President</p>
    </div>
    <ul class="contact-list">
      <li>
        <svg viewBox="0 0 14 14"><rect width="14" height="14" rx="2" fill="#2f4fc4"/><path d="M4 3.5c.6-.4 1.1 0 1.4.6l.4.9c.2.4 0 .7-.3 1-.2.2 0 .6.5 1.1s.9.7 1.1.5c.3-.3.6-.5 1-.3l.9.4c.6.3 1 .8.6 1.4-.5.8-1.6 1-2.9.2-1-.6-2-1.6-2.6-2.6-.8-1.3-.6-2.4.2-2.9z" fill="#fff"/></svg>
        909-555-0148
      </li>
      <li>
        <svg viewBox="0 0 14 14"><rect width="14" height="14" rx="2" fill="#2f4fc4"/><rect x="4" y="3" width="6" height="3" fill="#fff"/><rect x="3" y="6.5" width="8" height="3.5" rx="0.8" fill="#fff"/><rect x="4.5" y="9" width="5" height="2.5" fill="#fff"/></svg>
        909-555-0172
      </li>
      <li>
        <svg viewBox="0 0 14 14"><rect width="14" height="14" rx="2" fill="#2f4fc4"/><rect x="4.5" y="2.5" width="5" height="9" rx="1" fill="#fff"/><rect x="5.5" y="3.8" width="3" height="5" fill="#2f4fc4"/></svg>
        626 555 0193
      </li>
      <li>
        <svg viewBox="0 0 14 14"><rect width="14" height="14" rx="2" fill="#2f4fc4"/><rect x="2.5" y="4" width="9" height="6" fill="#fff"/><path d="M2.5 4l4.5 3.5L11.5 4" fill="none" stroke="#2f4fc4" stroke-width="1"/></svg>
        daniel@orvelpantry.com
      </li>
    </ul>
    <p class="address">2480 W. 5th St<br>Ontario, CA 91762</p>
    <div class="web-band">www.orvelpantry.com</div>
  </section>

  <section class="card card-back" aria-label="Business card back">
    <p class="brand-name-large">orvel</p>
  </section>
</body>
</html>
```